Timber Crest Construction Needs business card

Hey we are in need of business card designs. I have upload our logo as a guideline, but free feel to run with it or come up with something unique.
Pls have fun with it and be creative. the name says it all!
i will give some directions after i see a few entries..
Updates
Logo source file has been uploaded..
Hey because of the logo is so colourful already.
Can we have a few submissions with less colour.
Also we are looking for clever/hidden/descriptive business card.

```html
<!DOCTYPE html>
<html lang="en">
<head>
<meta charset="utf-8">
<title>Timber Crest Construction – Business Card</title>
<link rel="stylesheet" href="https://fonts.googleapis.com/css2?family=Open+Sans:wght@400;600;700&display=swap">
<style>
  :root {
    --bg: #e9e6e2;
    --card: #ffffff;
    --sky: #55a8f2;
    --ink: #111111;
    --slate: #5b6264;
    --text: #1c1c1c;
    --rule: #b9b9b9;
  }
  * { box-sizing: border-box; margin: 0; padding: 0; }
  html, body { width: 1200px; height: 470px; overflow: hidden; }
  body {
    background: var(--bg);
    font-family: "Open Sans", Arial, sans-serif;
    position: relative;
  }
  .card {
    position: absolute;
    top: 85px;
    width: 540px;
    height: 300px;
    background: var(--card);
    box-shadow: 0 4px 14px rgba(0,0,0,0.18);
    overflow: hidden;
  }
  .card--front { left: 30px; }
  .card--back { left: 630px; }

  .swoosh { position: absolute; inset: 0; width: 100%; height: 100%; }

  .holder {
    position: absolute;
    top: 14px;
    left: 380px;
    color: #fff;
    font-weight: 700;
    font-size: 19px;
    line-height: 1.15;
  }

  .wordmark {
    position: absolute;
    display: flex;
    align-items: center;
    gap: 10px;
    color: var(--slate);
    font-weight: 600;
    letter-spacing: 0.5px;
    line-height: 1;
  }
  .wordmark__square { background: var(--slate); flex: none; }
  .wordmark__name { display: flex; flex-direction: column; }
  .wordmark__sub { letter-spacing: 2px; margin-top: 4px; }

  .card--front .wordmark { left: 34px; top: 112px; font-size: 28px; }
  .card--front .wordmark__square { width: 24px; height: 24px; }
  .card--front .wordmark__sub { font-size: 11px; }

  .card--back .wordmark { left: 50%; top: 50%; transform: translate(-50%, -50%); font-size: 38px; }
  .card--back .wordmark__square { width: 34px; height: 34px; }
  .card--back .wordmark__sub { font-size: 15px; }

  .contact {
    position: absolute;
    left: 30px;
    bottom: 22px;
    display: flex;
    gap: 14px;
    color: var(--text);
    font-size: 11.5px;
    font-weight: 600;
  }
  .contact__list { list-style: none; display: flex; flex-direction: column; gap: 4px; }
  .contact__list li { display: flex; align-items: center; gap: 5px; }
  .contact__list svg { width: 11px; height: 11px; flex: none; }
  .contact__address {
    border-left: 1px solid var(--rule);
    padding-left: 12px;
    font-style: normal;
    line-height: 1.45;
    padding-top: 12px;
    height: 60px;
  }
</style>
</head>
<body>

  <section class="card card--front">
    <svg class="swoosh" viewBox="0 0 540 300" preserveAspectRatio="none" aria-hidden="true">
      <path d="M0,0 H540 V205 C505,110 390,28 0,22 Z" fill="var(--sky)"/>
      <path d="M0,28 C390,36 505,118 540,215 V250 C500,132 390,44 0,34 Z" fill="var(--ink)"/>
    </svg>

    <p class="holder">Your Name<br>Title</p>

    <div class="wordmark">
      <span class="wordmark__square"></span>
      <span class="wordmark__name">TIMBER CREST<span class="wordmark__sub">CONSTRUCTION</span></span>
    </div>

    <div class="contact">
      <ul class="contact__list">
        <li>
          <svg viewBox="0 0 12 12"><path d="M3 1 L5 3.5 L4 4.8 C4.6 6.2 5.8 7.4 7.2 8 L8.5 7 L11 9 L9.8 11 C5.5 10.6 1.4 6.5 1 2.2 Z" fill="var(--ink)"/></svg>
          0400 555 182
        </li>
        <li>
          <svg viewBox="0 0 12 12"><path d="M3 1 L5 3.5 L4 4.8 C4.6 6.2 5.8 7.4 7.2 8 L8.5 7 L11 9 L9.8 11 C5.5 10.6 1.4 6.5 1 2.2 Z" fill="var(--ink)"/></svg>
          0400 555 182
        </li>
        <li>
          <svg viewBox="0 0 12 12"><rect x="1" y="2.5" width="10" height="7" fill="var(--ink)"/><path d="M1 2.5 L6 6.5 L11 2.5" stroke="#fff" stroke-width="1" fill="none"/></svg>
          hello@timbercrestbuild.com
        </li>
        <li>
          <svg viewBox="0 0 12 12"><circle cx="6" cy="6" r="5" fill="none" stroke="var(--ink)" stroke-width="1.2"/><ellipse cx="6" cy="6" rx="2.2" ry="5" fill="none" stroke="var(--ink)" stroke-width="1"/><path d="M1 6 H11" stroke="var(--ink)" stroke-width="1"/></svg>
          www.timbercrestbuild.com
        </li>
      </ul>
      <address class="contact__address">Street Name City Name<br>State Zipcode</address>
    </div>
  </section>

  <section class="card card--back">
    <div class="wordmark">
      <span class="wordmark__square"></span>
      <span class="wordmark__name">TIMBER CREST<span class="wordmark__sub">CONSTRUCTION</span></span>
    </div>
  </section>

</body>
</html>
```